Tech business card design

We need an amazing business card design for our new business 'Pexla' a marketing tech startup based in Sydney, Australia. We provide an online marketplace for businesses to search and buy advertising media, connect with service providers and learn more about marketing. We wish to communicate 'cool tech', reliability and professionalism and design based around our logo.

Target Market(s)

Business Owners

Contact Information for Business Card

Name
Position
Email Address
Website
Phone Number

Font styles to use
Other font styles liked:
• Avenir & Avenir Next

Colors

Designer to choose colors to be used in the design.

```html
<!DOCTYPE html>
<html lang="en">
<head>
<meta charset="utf-8">
<title>Pexla business card</title>
<link href="https://fonts.googleapis.com/css2?family=Arimo:wght@400;700&display=swap" rel="stylesheet">
<style>
  :root {
    --stage: #1c1c1e;
    --card: #ffffff;
    --navy: #1c2150;
    --grey: #8a8a8a;
    --rule: #b5b5b5;
    --ink: #1a1a1a;
  }
  * { margin: 0; padding: 0; box-sizing: border-box; }
  html, body { width: 1200px; height: 803px; overflow: hidden; }
  body {
    background: var(--stage);
    font-family: "Arimo", Arial, sans-serif;
    display: flex;
    align-items: center;
    justify-content: center;
    gap: 50px;
  }
  .card {
    position: relative;
    width: 525px;
    height: 300px;
    background: var(--card);
    overflow: hidden;
    box-shadow: 0 10px 30px rgba(0,0,0,.5);
  }
  .card__art { position: absolute; inset: 0; }
  .wordmark {
    position: absolute;
    color: var(--navy);
    font-weight: 700;
    letter-spacing: -1px;
    line-height: 1;
  }
  .wordmark sup { font-size: 0.16em; letter-spacing: 0; vertical-align: top; margin-left: 4px; }
  .card--back .wordmark { top: 22px; right: 34px; font-size: 64px; }
  .card--front .wordmark { top: 74px; left: 0; right: 0; text-align: center; font-size: 118px; }

  .holder { position: absolute; left: 30px; top: 161px; color: var(--navy); }
  .holder__name { font-weight: 700; font-size: 16px; letter-spacing: .5px; }
  .holder__role { font-weight: 700; font-size: 12px; color: var(--ink); margin: 3px 0 0 8px; }
  .contact { position: absolute; left: 30px; top: 205px; list-style: none; font-size: 13px; color: var(--ink); }
  .contact li { display: flex; align-items: center; gap: 5px; margin-bottom: 3px; }
  .contact svg { width: 11px; height: 11px; fill: var(--ink); }
  .address { position: absolute; right: 16px; top: 140px; text-align: right; font-size: 12px; line-height: 1.35; color: var(--ink); }
  .web { position: absolute; right: 18px; top: 187px; font-size: 11px; letter-spacing: 3px; color: #fff; font-weight: 700; }
</style>
</head>
<body>
  <section class="card card--back">
    <svg class="card__art" viewBox="0 0 525 300" aria-hidden="true">
      <line x1="215" y1="118" x2="525" y2="118" stroke="var(--rule)" stroke-width="1.2"/>
      <line x1="128" y1="180" x2="330" y2="180" stroke="var(--rule)" stroke-width="1.2"/>
      <polygon points="525,184 337,184 306,254 0,254 0,266 314,266 345,202 525,202" fill="var(--navy)"/>
      <polygon points="0,271 320,271 314,279 0,279" fill="var(--grey)"/>
    </svg>
    <div class="wordmark">pexla<sup>TM</sup></div>
    <div class="address">Street Name, City Name<br>Zipcode:012345</div>
    <div class="web">www.pexla.com</div>
    <div class="holder">
      <p class="holder__name">JOHN SMITH</p>
      <p class="holder__role">Position</p>
    </div>
    <ul class="contact">
      <li><svg viewBox="0 0 24 24"><path d="M6.6 10.8a15 15 0 0 0 6.6 6.6l2.2-2.2c.3-.3.7-.4 1-.2 1.1.4 2.3.6 3.6.6.6 0 1 .4 1 1V20c0 .6-.4 1-1 1A17 17 0 0 1 3 4c0-.6.4-1 1-1h3.5c.6 0 1 .4 1 1 0 1.3.2 2.5.6 3.6.1.3 0 .7-.2 1z"/></svg>012-345-6789</li>
      <li><svg viewBox="0 0 24 24"><path d="M2 5h20v14H2z M3 6l9 7 9-7" fill="none" stroke="#1a1a1a" stroke-width="2"/></svg>info@pexla.com</li>
    </ul>
  </section>

  <section class="card card--front">
    <svg class="card__art" viewBox="0 0 525 300" aria-hidden="true">
      <rect x="0" y="222" width="525" height="40" fill="var(--navy)"/>
      <line x1="0" y1="282" x2="525" y2="282" stroke="var(--navy)" stroke-width="2"/>
    </svg>
    <div class="wordmark">pexla<sup>TM</sup></div>
  </section>
</body>
</html>
```